Business Card Design For A Renovation Contractor Company

We need a business card for a new company based in Singapore, our company name is "RB Tolvane". We are a renovation contractor that builds designs into reality. We build more of F&B restaurants, retail stores and commercial offices. We work very closely with designers. The final design should communicate to our client that we are a company that you can trust, that will plan and complete your project without giving you a headache. I like my client to remember my company as "RB". The beauty of SIMPLE is important.

Industry/Entity Type

Contractor

Requirements
Nice to have
• Black or Red base

```html
<!DOCTYPE html>
<html lang="en">
<head>
<meta charset="utf-8">
<title>RB Tolvane — Business Cards</title>
<link rel="stylesheet" href="https://fonts.googleapis.com/css2?family=Questrial&display=swap">
<style>
  :root {
    --ink: #1a1a1a;
    --red: #e0262b;
    --grey: #555555;
    --paper: #ffffff;
    --backdrop: #ececec;
    --rule: #8a8a8a;
  }
  * { margin: 0; padding: 0; box-sizing: border-box; }
  html, body { width: 1200px; height: 720px; overflow: hidden; }
  body {
    background: var(--backdrop);
    font-family: "Questrial", "Century Gothic", sans-serif;
    color: var(--ink);
    position: relative;
  }
  .card {
    position: absolute;
    width: 560px;
    height: 320px;
    background: var(--paper);
    box-shadow: 0 6px 18px rgba(0,0,0,0.18);
  }
  .card--front { left: 40px; top: 40px; }
  .card--back { left: 600px; top: 360px; }

  /* Front card */
  .wordmark { position: absolute; left: 34px; top: 44px; }
  .wordmark__name { font-size: 34px; line-height: 1; color: var(--ink); letter-spacing: -0.5px; }
  .wordmark__tagline {
    margin-top: 4px; padding-top: 2px;
    border-top: 1.5px solid var(--rule);
    font-size: 14px; color: var(--grey); letter-spacing: 0.3px;
  }
  .person { position: absolute; left: 34px; top: 132px; }
  .person__name { font-size: 19px; color: var(--red); font-weight: bold; }
  .person__title { font-size: 14px; color: var(--grey); margin-top: 1px; }
  .contacts { position: absolute; left: 34px; top: 182px; list-style: none; font-size: 14px; color: var(--grey); line-height: 1.45; }
  .contacts__label { color: var(--red); display: inline-block; width: 22px; }
  .address { position: absolute; left: 34px; top: 268px; font-size: 13px; color: var(--grey); line-height: 1.3; }
  .card__mark { position: absolute; right: 40px; top: 40px; }

  /* Back card */
  .back { position: absolute; inset: 0; display: flex; flex-direction: column; align-items: center; }
  .back__mark { margin-top: 38px; }
  .back__wordmark { position: static; margin-top: 12px; text-align: center; }
  .back__wordmark .wordmark__name { font-size: 46px; }
  .back__wordmark .wordmark__tagline { font-size: 19px; }
  .back__web { margin-top: 34px; font-size: 16px; letter-spacing: 3px; color: var(--ink); }
</style>
</head>
<body>
  <section class="card card--front" aria-label="Business card front">
    <div class="wordmark">
      <div class="wordmark__name">RB Tolvane</div>
      <div class="wordmark__tagline">turning designs into spaces</div>
    </div>
    <div class="person">
      <div class="person__name">Your Name</div>
      <div class="person__title">Title</div>
    </div>
    <ul class="contacts">
      <li><span class="contacts__label">P:</span>650-218-4407</li>
      <li><span class="contacts__label">C:</span>650-318-9902</li>
      <li><span class="contacts__label">E:</span>info@rbtolvane.com</li>
      <li><span class="contacts__label">W:</span>www.rbtolvane.com</li>
    </ul>
    <div class="address">Door No. Street Name<br>City Name, State, Zip Code</div>
    <svg class="card__mark" width="200" height="200" viewBox="0 0 200 200" aria-hidden="true">
      <circle cx="100" cy="100" r="92" fill="none" stroke="var(--ink)" stroke-width="12"/>
    </svg>
  </section>

  <section class="card card--back" aria-label="Business card back">
    <div class="back">
      <svg class="back__mark" width="90" height="90" viewBox="0 0 90 90" aria-hidden="true">
        <circle cx="45" cy="45" r="40" fill="none" stroke="var(--ink)" stroke-width="6"/>
      </svg>
      <div class="wordmark back__wordmark">
        <div class="wordmark__name">RB Tolvane</div>
        <div class="wordmark__tagline">turning designs into spaces</div>
      </div>
      <div class="back__web">www.rbtolvane.com</div>
    </div>
  </section>
</body>
</html>
```